Using attached logo that has been created

Business card with logo that's attached. Maybe with water or the cartoon van in background. Looking for it to not be so plain and not too white.
Information to include;
Rodney Ashcombe
(555) 218-7730
Info@bramleypipeworks.example
www.bramleypipeworks.example
License # 4627195
Looking forward to the designs u come up with.
Thank you!
-Delphine
Target Market(s)
Plumbing
Industry/Entity Type
Plumbing
Contact Information for Business Card
Listed above

```html
<!DOCTYPE html>
<html lang="en">
<head>
<meta charset="utf-8">
<title>Bramley Pipeworks Business Card</title>
<link rel="stylesheet" href="https://fonts.googleapis.com/css2?family=Montserrat:wght@400;500;700&display=swap">
<style>
  :root {
    --backdrop: #d1d5d7;
    --card: #f3f3f1;
    --brand-blue: #1b55c0;
    --edge-blue: #1a4cb0;
    --text-grey: #6d6d6d;
    --art-blue: #2f6fd6;
    --art-tan: #a88a5e;
    --art-skin: #c99172;
  }
  * { box-sizing: border-box; margin: 0; padding: 0; }
  html, body { width: 1200px; height: 1051px; overflow: hidden; }
  body {
    background: var(--backdrop);
    font-family: "Montserrat", sans-serif;
    display: flex;
    flex-direction: column;
    align-items: center;
    justify-content: center;
    gap: 70px;
  }
  .card {
    width: 700px;
    height: 400px;
    background: var(--card);
    border-bottom: 6px solid var(--edge-blue);
    box-shadow: 0 18px 40px rgba(0,0,0,.18);
    position: relative;
    display: flex;
    align-items: center;
  }
  .brand {
    display: flex;
    flex-direction: column;
    align-items: center;
    gap: 12px;
  }
  .brand-art {
    border-radius: 50% 50% 12px 12px;
    background: linear-gradient(180deg, var(--art-skin) 0%, var(--art-blue) 30%, var(--art-blue) 55%, var(--art-tan) 100%);
  }
  .brand-name {
    color: var(--brand-blue);
    font-weight: 700;
    text-transform: uppercase;
    letter-spacing: .04em;
    text-align: center;
    line-height: 1.1;
  }
  .card-front .brand { width: 315px; }
  .card-front .brand-art { width: 110px; height: 160px; }
  .card-front .brand-name { font-size: 22px; }
  .divider {
    width: 2px;
    height: 240px;
    background: var(--brand-blue);
  }
  .contact { padding-left: 40px; }
  .contact-name {
    color: var(--brand-blue);
    font-weight: 700;
    font-size: 26px;
    text-transform: uppercase;
    letter-spacing: .02em;
  }
  .license {
    color: var(--text-grey);
    font-size: 16px;
    margin: 6px 0 22px;
  }
  .contact-list { list-style: none; }
  .contact-list li {
    display: flex;
    align-items: center;
    gap: 10px;
    color: var(--text-grey);
    font-size: 16px;
    margin-bottom: 8px;
  }
  .contact-list svg { width: 14px; height: 14px; fill: var(--brand-blue); flex: none; }
  .card-back { justify-content: center; }
  .card-back .brand-art { width: 150px; height: 215px; }
  .card-back .brand-name { font-size: 34px; }
</style>
</head>
<body>
  <section class="card card-front">
    <div class="brand">
      <div class="brand-art" role="img" aria-label="Cartoon mascot illustration of a plumber holding a pipe wrench and a circular saw"></div>
      <div class="brand-name">Bramley Pipeworks</div>
    </div>
    <div class="divider"></div>
    <div class="contact">
      <h1 class="contact-name">Rodney Ashcombe</h1>
      <p class="license">License # 4627195</p>
      <ul class="contact-list">
        <li>
          <svg viewBox="0 0 24 24" aria-hidden="true"><path d="M6.6 10.8a15.1 15.1 0 0 0 6.6 6.6l2.2-2.2a1 1 0 0 1 1-.25 11.4 11.4 0 0 0 3.6.57 1 1 0 0 1 1 1V20a1 1 0 0 1-1 1A17 17 0 0 1 3 4a1 1 0 0 1 1-1h3.5a1 1 0 0 1 1 1c0 1.25.2 2.45.57 3.57a1 1 0 0 1-.25 1z"/></svg>
          (555) 218-7730
        </li>
        <li>
          <svg viewBox="0 0 24 24" aria-hidden="true"><path d="M2 5h20v14H2z" opacity=".35"/><path d="M2 5l10 8 10-8v3l-10 8L2 8z"/></svg>
          Info@bramleypipeworks.example
        </li>
        <li>
          <svg viewBox="0 0 24 24" aria-hidden="true"><circle cx="12" cy="12" r="10"/></svg>
          www.bramleypipeworks.example
        </li>
      </ul>
    </div>
  </section>

  <section class="card card-back">
    <div class="brand">
      <div class="brand-art" role="img" aria-label="Cartoon mascot illustration of a plumber holding a pipe wrench and a circular saw"></div>
      <div class="brand-name">Bramley Pipeworks</div>
    </div>
  </section>
</body>
</html>
```